Pebble Hop - mobile play centre poster designs

Who are we - we are a mobile playground business that specialises in providing entertainment to children in a safe, clean environment either at home or in a function centre. Brief - create 4 different signs to be displayed on our playgrounds. Please find attached 3 photos from our competitors to use as a guide. Corflute sign - size A1 Toddler zone - size A1 Playground rules - size A4 No climbing - size 20cmx8cm sending through photos and documents now.
Colors
Designer to choose colors to be used in the design.
Requirements
Must have
- Colour, be very specific with the rules, pictures

```html
<!DOCTYPE html>
<html lang="en">
<head>
<meta charset="utf-8">
<title>Pebble Hop – No Climbing Sign</title>
<link href="https://fonts.googleapis.com/css2?family=Anton&family=Fredoka:wght@600&display=swap" rel="stylesheet">
<style>
  :root {
    --backdrop: #e4e4e4;
    --frame-yellow: #f6d21c;
    --frame-yellow-dark: #e2b90f;
    --bamboo-green: #a9c83c;
    --bamboo-dark: #7f9c24;
    --panel-light: #fbf5d6;
    --panel-leaf: #d9e6c4;
    --sign-red: #e8262a;
    --sign-orange: #f58a1f;
    --brand-green: #4aa63a;
    --brand-sub: #6a5a86;
    --net-tone: #c9c2b5;
  }
  html, body {
    margin: 0;
    padding: 0;
    width: 1200px;
    height: 603px;
    overflow: hidden;
    background: var(--backdrop);
  }
  .canvas {
    position: relative;
    width: 1200px;
    height: 603px;
  }
  .sign {
    position: absolute;
    left: 50px;
    top: 79px;
    width: 1100px;
    height: 445px;
  }
  .headline {
    font-family: "Anton", "Oswald", sans-serif;
  }
  .brand-name {
    font-family: "Fredoka", "Baloo 2", sans-serif;
    font-weight: 600;
  }
  .brand-tagline {
    font-family: "Fredoka", "Baloo 2", sans-serif;
    font-weight: 600;
    letter-spacing: 1px;
  }
</style>
</head>
<body>
<main class="canvas">
  <svg class="sign" viewBox="0 0 1100 445" xmlns="http://www.w3.org/2000/svg">
    <defs>
      <linearGradient id="jungle-wash" x1="0" y1="0" x2="0" y2="1">
        <stop offset="0" stop-color="#eaf0d8"/>
        <stop offset="0.55" stop-color="#fbf5d6"/>
        <stop offset="1" stop-color="#e1ebc8"/>
      </linearGradient>
      <linearGradient id="bamboo-h" x1="0" y1="0" x2="0" y2="1">
        <stop offset="0" stop-color="#c4dc5a"/>
        <stop offset="1" stop-color="#86a52a"/>
      </linearGradient>
      <linearGradient id="bamboo-v" x1="0" y1="0" x2="1" y2="0">
        <stop offset="0" stop-color="#c4dc5a"/>
        <stop offset="1" stop-color="#86a52a"/>
      </linearGradient>
    </defs>

    <!-- outer yellow board -->
    <rect class="board" x="0" y="0" width="1100" height="445" fill="var(--frame-yellow)"/>
    <rect class="board-edge" x="0" y="425" width="1100" height="20" fill="var(--frame-yellow-dark)"/>

    <!-- jungle backdrop area -->
    <rect class="jungle-backdrop" x="46" y="22" width="1008" height="398" fill="url(#jungle-wash)"
          role="img" aria-label="Soft jungle background with pale leaves and misty hills"/>

    <!-- bamboo frame -->
    <g class="bamboo-frame" role="img" aria-label="Bamboo pole frame">
      <rect x="30" y="14" width="1040" height="14" rx="7" fill="url(#bamboo-h)"/>
      <rect x="30" y="414" width="1040" height="14" rx="7" fill="url(#bamboo-h)"/>
      <rect x="30" y="8" width="16" height="428" rx="8" fill="url(#bamboo-v)"/>
      <rect x="1054" y="8" width="16" height="428" rx="8" fill="url(#bamboo-v)"/>
    </g>

    <!-- pictogram: climbing child on net, crossed out -->
    <rect class="pictogram" x="110" y="168" width="160" height="112" rx="6" fill="var(--net-tone)" opacity="0.75"
          role="img" aria-label="Child climbing a rope net"/>
    <line class="prohibit-slash" x1="322" y1="128" x2="92" y2="325"
          stroke="var(--sign-red)" stroke-width="5" stroke-linecap="round"/>

    <!-- brand -->
    <text class="brand-name" x="345" y="112" font-size="40" fill="var(--brand-green)">Pebble Hop</text>
    <text class="brand-tagline" x="347" y="138" font-size="17" fill="var(--brand-sub)">MOBILE PLAY CENTRE</text>

    <!-- headline -->
    <text class="headline" x="345" y="305" font-size="150" textLength="685" lengthAdjust="spacingAndGlyphs"><tspan fill="var(--sign-red)">NO </tspan><tspan fill="var(--sign-orange)">CLIMBING</tspan></text>
  </svg>
</main>
</body>
</html>
```